Web Site Design and Business Card design for Recruiting Company

There are three major tasks in this project:
1) I need to re-design my newly created website www.talvoro.net using the same logo but creating a totally different recruiting template that will apply better for a recruitment site. I want to use the elements of the Talvoro Network logo (which is the road junction) and red, black and gray colors throughout the website. I need someone to both design and launch the site...
2) I would also like to design a double sided business card using the same logo/colors and elements as described above
3) I would also like to have a small thumbnail logo created. As our large logo cannot be previewed easily on the Pelmwork or on Google Chrome tab images

The design should be contemporary, minimalist and slick

```html
<!DOCTYPE html>
<html lang="en">
<head>
<meta charset="utf-8">
<title>Talvoro Network</title>
<link href="https://fonts.googleapis.com/css2?family=Lato:wght@400;700&display=swap" rel="stylesheet">
<style>
:root{
  --red:#e0121b;
  --red-deep:#c4000a;
  --ink:#111111;
  --dark:#141414;
  --gray:#f0f0f0;
  --mid:#777777;
  --white:#ffffff;
}
*{margin:0;padding:0;box-sizing:border-box}
html,body{width:1200px;height:2965px;overflow:hidden}
body{font-family:'Lato',sans-serif;color:var(--ink);background:var(--white);position:relative}
.abs{position:absolute}
.center{text-align:center}

/* header */
.site-header{left:0;top:0;width:1200px;height:105px;background:var(--white)}
.brand{left:173px;top:36px;font-size:22px;font-weight:700;color:var(--ink);letter-spacing:.5px}
.brand .dot{display:inline-block;width:12px;height:12px;background:var(--red);margin-right:8px;vertical-align:1px}
.nav a{position:absolute;top:38px;font-size:16.5px;font-weight:700;color:var(--ink);text-decoration:none;letter-spacing:.2px}
.nav a.active{color:var(--red)}
.nav-bar{left:472px;top:100px;width:61px;height:5px;background:var(--red)}

/* hero */
.hero{left:0;top:105px;width:1200px;height:589px;background:linear-gradient(180deg,#d8d8d8 0%,#9a9a9a 35%,#4d4d4d 70%,#2c2c2c 100%)}
.hero-circle{left:128px;top:207px;width:380px;height:380px;border-radius:50%;background:rgba(240,240,240,.93)}
.hero-title{left:128px;width:380px;font-size:37px;color:var(--ink)}
.hero-name{left:128px;width:380px;font-size:38px;font-weight:700;color:var(--red)}
.hero-sub{left:128px;width:380px;font-size:18px;line-height:27px;color:#333}
.btn-outline-red{border:2px solid var(--red);color:var(--red);font-size:17px;display:flex;align-items:center;justify-content:center}
.btn-outline-white{border:2px solid var(--white);color:var(--white);font-size:17px;display:flex;align-items:center;justify-content:center}
.arrow{stroke:#e6e6e6;stroke-width:2;fill:none}

/* sections */
.light-band{left:0;top:694px;width:1200px;height:1681px;background:linear-gradient(180deg,#ececec 0%,#f7f7f7 25%,#f7f7f7 28%,var(--gray) 40%)}
.section-title{font-size:37px;font-weight:700;color:var(--ink);width:1200px;left:0}
.rule{height:3px;background:var(--ink)}
.about-text{left:190px;width:830px;font-size:19px;line-height:35px;color:#333}

/* services */
.service{color:var(--white)}
.svc-it{left:0;top:1275px;width:384px;height:447px;background:linear-gradient(135deg,#3a3a3a,#1d1d1d 60%,#2a2a2a)}
.svc-tel{left:388px;top:1241px;width:404px;height:517px;background:linear-gradient(160deg,#ff1a22,#d5000b 55%,#b8000a)}
.svc-acc{left:796px;top:1275px;width:404px;height:447px;background:linear-gradient(200deg,#3d3d3d,#222 55%,#303030)}
.svc-head{position:absolute;left:0;width:100%;text-align:center;font-size:25px;line-height:25px;font-weight:700;letter-spacing:.3px}
.svc-list{position:absolute;left:0;width:100%;text-align:center;font-size:16px;line-height:31px;font-weight:700}
.svc-icon{position:absolute;fill:none;stroke:var(--white);stroke-width:2.5}

/* posts */
.posts-title{left:167px;top:1822px;font-size:37px;font-weight:700}
.post{top:1910px;width:283px;height:362px;background:var(--white);border:1.5px solid #cfcfcf}
.post-img{position:absolute;left:11px;top:12px;width:259px;height:153px}
.post-t{position:absolute;left:26px;top:177px;width:240px;font-size:16px;line-height:19px;font-weight:700;color:#222}
.post-meta{position:absolute;left:26px;top:221px;font-size:12.5px;font-weight:700;color:var(--red)}
.post-body{position:absolute;left:26px;top:244px;width:236px;font-size:12.5px;line-height:17px;color:var(--mid)}
.post-btn{position:absolute;left:26px;top:308px;width:110px;height:33px;border:2px solid var(--red);font-size:12.5px;font-weight:700;color:var(--ink);display:flex;align-items:center;justify-content:center}

/* contact */
.contact{left:0;top:2375px;width:1200px;height:443px;background:var(--dark)}
.field{border:1.5px solid #8a8a8a;border-radius:2px;color:#e8e8e8;font-size:14px;padding:12px 16px;background:transparent}
.submit{left:523px;top:2707px;width:154px;height:43px;background:var(--red-deep);color:var(--white);font-size:17px;display:flex;align-items:center;justify-content:center}

/* footer */
.foot-link{top:2863px;font-size:17px;font-weight:700;color:var(--ink)}
.copy{left:173px;top:2900px;font-size:14px;color:#333}
.social{top:2849px;width:42px;height:42px;border-radius:50%;background:var(--red-deep)}
</style>
</head>
<body>

<header class="abs site-header">
  <div class="abs brand"><span class="dot"></span>Talvoro Network</div>
  <nav class="nav">
    <a class="active" style="left:478px">HOME</a>
    <a style="left:576px">ABOUT US</a>
    <a style="left:709px">SERVICES</a>
    <a style="left:837px">CONTACT US</a>
  </nav>
  <svg class="abs" style="left:982px;top:36px" width="22" height="22" viewBox="0 0 22 22" aria-label="Search"><circle cx="9" cy="9" r="6.5" fill="none" stroke="#999" stroke-width="2.5"/><line x1="14" y1="14" x2="20" y2="20" stroke="#999" stroke-width="3"/></svg>
  <div class="abs nav-bar"></div>
</header>

<section class="abs hero" role="img" aria-label="Black and white aerial photo of the Atlanta skyline with highways"></section>
<svg class="abs" style="left:64px;top:362px" width="30" height="60" viewBox="0 0 30 60"><polyline class="arrow" points="27,2 3,30 27,58"/></svg>
<svg class="abs" style="left:1088px;top:362px" width="30" height="60" viewBox="0 0 30 60"><polyline class="arrow" points="3,2 27,30 3,58"/></svg>
<div class="abs hero-circle"></div>
<div class="abs hero-title center" style="top:300px">Welcome to</div>
<div class="abs hero-name center" style="top:343px">Talvoro Network</div>
<div class="abs hero-sub center" style="top:391px">Atlanta based talent advisory,<br>recruiting and staffing firm.</div>
<div class="abs btn-outline-red" style="left:235px;top:462px;width:162px;height:48px">LEARN MORE</div>

<div class="abs light-band"></div>

<h2 class="abs section-title center" style="top:762px">About <span style="color:var(--red)">Talvoro</span> Network</h2>
<div class="abs rule" style="left:566px;top:816px;width:74px"></div>
<p class="abs about-text center" style="top:835px">Talvoro Network LLC is an Atlanta based talent advisory, recruiting and staffing firm. We help companies find skilled professionals within the shortest time frames though our unique network of business and personal connections nationwide and overseas.</p>
<div class="abs btn-outline-red" style="left:524px;top:965px;width:162px;height:48px">LEARN MORE</div>

<h2 class="abs section-title center" style="top:1150px;font-size:41px">Our Services</h2>
<div class="abs rule" style="left:561px;top:1205px;width:74px"></div>

<div class="abs service svc-it" role="img" aria-label="Photo of an IT professional at a computer, dark overlay">
  <svg class="svc-icon" style="left:172px;top:26px" width="70" height="64" viewBox="0 0 70 64"><circle cx="34" cy="32" r="8"/><circle cx="8" cy="8" r="6"/><circle cx="62" cy="8" r="6"/><circle cx="8" cy="56" r="6"/><circle cx="52" cy="58" r="5"/><line x1="12" y1="12" x2="28" y2="27"/><line x1="58" y1="12" x2="40" y2="27"/><line x1="12" y1="52" x2="28" y2="37"/><line x1="48" y1="54" x2="39" y2="38"/></svg>
  <div class="svc-head" style="top:106px">INFORMATION<br>TECHNOLOGY</div>
  <div class="svc-list" style="top:168px">Project Management<br>Web and Application Development<br>Network Administration<br>System Engineering and Administration<br>Software Engineering</div>
  <div class="abs btn-outline-white" style="left:121px;top:354px;width:161px;height:49px">LEARN MORE</div>
</div>

<div class="abs service svc-tel" role="img" aria-label="Photo of a telecom engineer on a cell tower, red overlay">
  <svg class="svc-icon" style="left:168px;top:38px" width="68" height="66" viewBox="0 0 68 66"><path d="M14 30 V24 a20 20 0 0 1 40 0 V30"/><rect x="9" y="26" width="9" height="14" rx="3"/><rect x="50" y="26" width="9" height="14" rx="3"/><path d="M54 40 q0 8 -14 9"/><path d="M4 64 q2 -16 30 -16 q28 0 30 16 z"/></svg>
  <div class="svc-head" style="top:128px">TELECOMMUNICATIONS</div>
  <div class="svc-list" style="top:175px">Project Management<br>Construction Management<br>Site Acquisition<br>L&amp;A Installation and Civil Work<br>RF Engineering and Network Design<br>Cell Site Integration</div>
  <div class="abs btn-outline-white" style="left:121px;top:384px;width:162px;height:49px">LEARN MORE</div>
</div>

<div class="abs service svc-acc" role="img" aria-label="Photo of a desk with financial charts and a calculator, dark overlay">
  <svg class="svc-icon" style="left:168px;top:28px" width="60" height="56" viewBox="0 0 60 56"><rect x="2" y="2" width="56" height="38"/><line x1="30" y1="40" x2="30" y2="50"/><line x1="16" y1="52" x2="44" y2="52"/><rect x="13" y="22" width="6" height="12"/><rect x="23" y="16" width="6" height="18"/><rect x="33" y="10" width="6" height="24"/><rect x="43" y="20" width="6" height="14"/></svg>
  <div class="svc-head" style="top:101px">ACCOUNTING &amp;<br>FINANCE</div>
  <div class="svc-list" style="top:160px">Financial Planning<br>Financial Management<br>Certified Public Accounting (CPA)<br>Audit<br>Cost Accounting</div>
  <div class="abs btn-outline-white" style="left:117px;top:346px;width:162px;height:48px">LEARN MORE</div>
</div>

<h2 class="abs posts-title">Recent Posts</h2>
<div class="abs rule" style="left:169px;top:1876px;width:74px"></div>

<article class="abs post" style="left:161px">
  <div class="post-img" role="img" aria-label="Photo of a smiling businesswoman shaking hands in an office" style="background:linear-gradient(135deg,#b9b9b6,#7d7d78 60%,#4e4e4c)"></div>
  <div class="post-t">Duis non nunc Nulla rhoncus dictum metus Curabitur</div>
  <div class="post-meta">By Author Name &nbsp;|&nbsp; JAN 20, 2019</div>
  <div class="post-body">Duis non nunc Nulla rhoncus dictum metus Curabitur tristique mi condimen-tum orci Phasellus pellentesq</div>
  <div class="post-btn">READ MORE</div>
</article>
<article class="abs post" style="left:462px">
  <div class="post-img" role="img" aria-label="Photo of a smiling man at a job interview" style="background:linear-gradient(135deg,#6a5a4e,#3b4a44 55%,#7a7370)"></div>
  <div class="post-t">Duis non nunc Nulla rhoncus dictum metus Curabitur</div>
  <div class="post-meta">By Author Name &nbsp;|&nbsp; JAN 20, 2019</div>
  <div class="post-body">Duis non nunc Nulla rhoncus dictum metus Curabitur tristique mi condimen-tum orci Phasellus pellentesq</div>
  <div class="post-btn">READ MORE</div>
</article>
<article class="abs post" style="left:761px">
  <div class="post-img" role="img" aria-label="Photo of a hand selecting people icons on a digital network" style="background:linear-gradient(135deg,#1f7a80,#2f8f95 45%,#2b3d55)"></div>
  <div class="post-t">Duis non nunc Nulla rhoncus dictum metus Curabitur</div>
  <div class="post-meta">By Author Name &nbsp;|&nbsp; JAN 20, 2019</div>
  <div class="post-body">Duis non nunc Nulla rhoncus dictum metus Curabitur tristique mi condimen-tum orci Phasellus pellentesq</div>
  <div class="post-btn">READ MORE</div>
</article>

<section class="abs contact">
  <h2 class="abs center" style="left:0;width:1200px;top:44px;font-size:37px;font-weight:700;color:var(--white)">Contact Us</h2>
  <div class="abs field" style="left:258px;top:117px;width:338px;height:43px">First Name</div>
  <div class="abs field" style="left:605px;top:117px;width:339px;height:43px">Last Name</div>
  <div class="abs field" style="left:258px;top:166px;width:338px;height:43px">Email address</div>
  <div class="abs field" style="left:605px;top:166px;width:339px;height:43px">Phone Number</div>
  <div class="abs field" style="left:258px;top:221px;width:686px;height:92px">Type Message</div>
</section>
<div class="abs submit">SUBMIT</div>

<footer>
  <div class="abs foot-link" style="left:173px">HOME</div>
  <div class="abs foot-link" style="left:270px">ABOUT US</div>
  <div class="abs foot-link" style="left:404px">SERVICES</div>
  <div class="abs foot-link" style="left:532px">CONTACT US</div>
  <div class="abs copy">© 2019 Company Name &nbsp;All right reserved</div>
  <div class="abs social" style="left:830px" aria-label="Social link"></div>
  <div class="abs social" style="left:879px" aria-label="Social link"></div>
  <div class="abs social" style="left:929px" aria-label="Social link"></div>
  <div class="abs social" style="left:978px" aria-label="Social link"></div>
</footer>

</body>
</html>
```